Barrister at Law needs Business Card Design

Need a business card design for Barrister at Law. Double sided. Simple Neil Thorsby and Barrister at Law on one side with contact details on the other side. I would like a professional design using Black or Platinum. Details on reverse side would include qualifications - Bcom-Llb and Acc Spec Commercial Litigation. I have attached the logo. Contact details would include address/ Po Box/ Phone/Fax/Mobile/email. I would like to use raised print or spot gloss.

```html
<!DOCTYPE html>
<html lang="en">
<head>
<meta charset="utf-8">
<title>Alex Raeburn – Barrister at Law business card</title>
<link href="https://fonts.googleapis.com/css2?family=Open+Sans:wght@400;600&display=swap" rel="stylesheet">
<style>
  :root {
    --backdrop: #e9e7e4;
    --card: #141414;
    --card-edge: #0a0a0a;
    --ink: #e6e6e6;
    --ink-soft: #bdbdbd;
    --accent: #1f8fd6;
    --gloss: #6a6a6a;
  }
  * { box-sizing: border-box; margin: 0; padding: 0; }
  html, body { width: 1200px; height: 814px; overflow: hidden; }
  body {
    background: var(--backdrop);
    font-family: "Open Sans", sans-serif;
    position: relative;
  }
  .card {
    position: absolute;
    top: 258px;
    width: 520px;
    height: 297px;
    background: var(--card);
    border: 1px solid var(--card-edge);
    box-shadow: 0 6px 18px rgba(0,0,0,.25);
  }
  .card--front { left: 60px; }
  .card--back { left: 620px; }

  .front-mark {
    position: absolute;
    inset: 0;
    display: flex;
    align-items: center;
    justify-content: center;
    gap: 12px;
    color: var(--gloss);
    font-size: 26px;
    font-weight: 600;
    letter-spacing: .5px;
  }
  .front-mark__dot {
    width: 16px; height: 16px;
    border-radius: 50%;
    background: var(--gloss);
  }

  .holder { position: absolute; left: 34px; top: 62px; }
  .holder__name {
    color: var(--accent);
    font-size: 17px;
    font-weight: 600;
    line-height: 1.2;
  }
  .holder__quals {
    color: var(--ink);
    font-size: 11.5px;
    margin-top: 3px;
  }
  .contacts { list-style: none; margin-top: 7px; }
  .contacts li {
    display: flex;
    align-items: center;
    gap: 8px;
    color: var(--ink-soft);
    font-size: 11px;
    line-height: 19px;
  }
  .contacts svg { width: 11px; height: 11px; fill: var(--accent); flex: none; }

  .rule {
    position: absolute;
    left: 250px; right: 34px; top: 99px;
    height: 1px;
    background: var(--accent);
  }
  .badge {
    position: absolute;
    right: 36px; top: 112px;
    width: 104px; height: 104px;
    border-radius: 50%;
    border: 3px solid var(--ink);
  }
  .address {
    position: absolute;
    right: 34px; bottom: 22px;
    text-align: right;
    color: var(--ink);
    font-size: 12px;
    line-height: 18px;
    font-style: normal;
  }
</style>
</head>
<body>
  <section class="card card--front" aria-label="Card front">
    <div class="front-mark"><span class="front-mark__dot"></span>Raeburn Chambers</div>
  </section>

  <section class="card card--back" aria-label="Card back">
    <div class="holder">
      <p class="holder__name">Alex Raeburn</p>
      <p class="holder__quals">Bcom-Llb&amp;Acc.Spec.(Comm Lit)</p>
      <ul class="contacts">
        <li><svg viewBox="0 0 12 12"><path d="M2.5 0.5l2 2.2-1.1 1.4c.8 1.7 2 2.9 3.6 3.7l1.4-1.1 2.2 2-1.3 2.4C5 10.7 1.1 6.8.4 1.8z"/></svg>614 302 7718</li>
        <li><svg viewBox="0 0 12 12"><path d="M3 0h6v12H3zM4 1.5v8h4v-8z"/></svg>614 302 7719</li>
        <li><svg viewBox="0 0 12 12"><path d="M3 0h6v3H3zM0 4h12v6h-2v2H2v-2H0zM3 8v3h6V8z"/></svg>478 215 6043</li>
        <li><svg viewBox="0 0 12 12"><path d="M0 2h12v8H0zM1 3l5 3.5L11 3z"/></svg>alex@raeburnchambers.com</li>
      </ul>
    </div>
    <div class="rule"></div>
    <div class="badge" role="img" aria-label="Accredited specialist badge"></div>
    <address class="address">
      42 Harbour Row<br>
      Brisbane, QLD 4000<br>
      www.raeburnchambers.com
    </address>
  </section>
</body>
</html>
```